The most modern business card ever !!!

Our company call “Vendalo”. Vendalo is a technology company specialized in cruises solutions. Out main product is a platform to reserve cruises. This is a revolutionary platform that make easier to travel agencies and final users to reserve cruises across dozen companies like tibba, wernu, hpv, dgb, etc..We are a “start up”, with a young team of developers and we want to transmit it.. For it, we want something different, a modern business card that represent cruises and technology.. When someone receive this card, this person should say: wowww this is different… this is modern… this is a cruise related company..
- diferent, modern
- traditions business card

```html
<!DOCTYPE html>
<html lang="en">
<head>
<meta charset="utf-8">
<title>Vendalo business card</title>
<link href="https://fonts.googleapis.com/css2?family=Poppins:wght@300;400;600;700&display=swap" rel="stylesheet">
<style>
  :root{
    --bg:#eeeeee;
    --teal-deep:#0c4a4c;
    --teal:#1f7a7a;
    --teal-light:#3f9c9c;
    --sky:#2fa9e0;
    --ink:#1b1f24;
    --paper:#ffffff;
    --tint:#e4f2f4;
    --muted:#5e6a70;
    --url:#a9dcdc;
  }
  *{box-sizing:border-box;margin:0;padding:0}
  html,body{width:1200px;height:885px;overflow:hidden}
  body{background:var(--bg);font-family:"Poppins",sans-serif;position:relative}

  .card{position:absolute;width:540px;height:310px;border-radius:6px;overflow:hidden;
        box-shadow:0 10px 30px rgba(0,0,0,.18)}

  .card--front{left:40px;top:288px;
    background:radial-gradient(ellipse at 50% 40%,var(--teal-light) 0%,var(--teal) 45%,var(--teal-deep) 100%)}
  .front__brand{position:absolute;left:0;right:0;top:112px;text-align:center}
  .brand-name{font-weight:700;font-size:50px;letter-spacing:1px;color:var(--ink);line-height:1}
  .front__url{margin-top:8px;font-weight:400;font-size:13px;letter-spacing:7px;color:var(--url)}

  .card--back{left:620px;top:288px;background:var(--paper)}
  .back__art{position:absolute;inset:0}
  .back__tab{position:absolute;left:26px;top:0;width:124px;height:10px;background:var(--teal)}
  .back__brand{position:absolute;left:26px;top:26px;font-weight:700;font-size:32px;color:var(--ink);line-height:1}
  .back__person{position:absolute;left:26px;top:76px}
  .person-name{font-weight:600;font-size:17px;letter-spacing:1px;color:var(--ink);line-height:1.2}
  .person-role{font-weight:400;font-size:8px;letter-spacing:2px;color:var(--muted);margin-top:3px}
  .person-icon{position:absolute;left:196px;top:72px;width:42px;height:42px;border-radius:50%;background:var(--sky);
    display:flex;align-items:center;justify-content:center}

  .contact{position:absolute;display:flex;align-items:center;gap:12px}
  .contact__icon{width:40px;height:40px;border-radius:50%;background:var(--sky);flex:none;
    display:flex;align-items:center;justify-content:center;box-shadow:0 2px 6px rgba(0,0,0,.2)}
  .contact__label{font-weight:600;font-size:15px;color:var(--ink);line-height:1.15}
  .contact__value{font-weight:400;font-size:10px;color:var(--ink);line-height:1.3}
  .contact--phone{left:101px;top:150px}
  .contact--mail{left:140px;top:200px}
  .contact--addr{left:179px;top:250px}
</style>
</head>
<body>
  <section class="card card--front">
    <div class="front__brand">
      <div class="brand-name">vendalo</div>
      <div class="front__url">www.vendalo.com</div>
    </div>
  </section>

  <section class="card card--back">
    <svg class="back__art" width="540" height="310" viewBox="0 0 540 310">
      <rect x="300" y="40" width="120" height="90" rx="18" fill="var(--tint)" opacity=".7"/>
      <rect x="400" y="110" width="110" height="80" rx="18" fill="var(--tint)"/>
      <rect x="360" y="190" width="130" height="90" rx="20" fill="var(--tint)" opacity=".7"/>
      <rect x="270" y="120" width="60" height="60" rx="14" fill="var(--tint)" opacity=".8"/>
      <polygon points="0,130 90,130 230,310 0,310" fill="var(--teal)"/>
      <polygon points="0,130 30,130 100,310 0,310" fill="var(--teal-deep)" opacity=".3"/>
    </svg>
    <div class="back__tab"></div>
    <div class="back__brand">vendalo</div>
    <div class="back__person">
      <div class="person-name">YOUR NAME</div>
      <div class="person-role">YOUR POSITION</div>
    </div>
    <div class="person-icon">
      <svg width="20" height="20" viewBox="0 0 20 20"><circle cx="10" cy="6" r="4" fill="var(--ink)"/><path d="M2 19c0-5 4-8 8-8s8 3 8 8z" fill="var(--ink)"/></svg>
    </div>

    <div class="contact contact--phone">
      <div class="contact__icon"><svg width="18" height="18" viewBox="0 0 24 24"><path d="M6.6 10.8a15 15 0 0 0 6.6 6.6l2.2-2.2c.3-.3.7-.4 1-.2 1.1.4 2.3.6 3.6.6.6 0 1 .4 1 1V20c0 .6-.4 1-1 1A17 17 0 0 1 3 4c0-.6.4-1 1-1h3.5c.6 0 1 .4 1 1 0 1.3.2 2.5.6 3.6.1.3 0 .7-.2 1z" fill="var(--ink)"/></svg></div>
      <div><div class="contact__label">Your Phone</div><div class="contact__value">+62-812-555-0147</div></div>
    </div>
    <div class="contact contact--mail">
      <div class="contact__icon"><svg width="18" height="18" viewBox="0 0 24 24"><rect x="3" y="5" width="18" height="14" rx="1" fill="none" stroke="var(--ink)" stroke-width="2"/><path d="M3 6l9 7 9-7" fill="none" stroke="var(--ink)" stroke-width="2"/></svg></div>
      <div><div class="contact__label">Your E-mail</div><div class="contact__value">hello@vendalo.com</div></div>
    </div>
    <div class="contact contact--addr">
      <div class="contact__icon"><svg width="18" height="18" viewBox="0 0 24 24"><path d="M12 2a7 7 0 0 0-7 7c0 5 7 13 7 13s7-8 7-13a7 7 0 0 0-7-7z" fill="var(--ink)"/><circle cx="12" cy="9" r="2.5" fill="var(--sky)"/></svg></div>
      <div><div class="contact__label">Your Adress</div><div class="contact__value">Harbor Lane 8, Portvale</div></div>
    </div>
  </section>
</body>
</html>
```